Yacht, Boats, Watersports company needs a redesign of business card

Hello Designers!
We are a Boat dealership company that sells fun in the water, we sell boats, Yachts, Kayaks and also yacht WaterSport toys. We are looking to redesign our business cards in to something a little bit more sophisticated. in a way that we can make better use of our company colors. I'm attaching a zipped file containing the company 3 sets of company logo which one is an horizontal another one is a vertical and also a chromed 3d logo. Also is included two set of business cards that we use and also some designs that i think it's interesting. We use PMS 2026c Orange and PMS 7687C Blue. I would like to see at least two different options with the orange as accent and also using blue as an accent color. It's really important for the business cards to have a font option and size that is legible to most people. Our current website is wwww.coralpennant.com. Please visit if you want to have a better feeling of the Boat dealership
You can send Single sided or double side options. We are now using single sided but we may be open for a double side option if we really like the design.
Target Market(s)
Marine, boat sales, yacht sales, water toys sales/
Contact Information for Business Card
Name: Dale Whitcombe
Address: 212 North Fenwick Lane,
Harbor Point, FL 33120
Phone: 954-731-8842
Fax: 954:731-8843
Cell: 954-382-1490
Email: dw@coralpennant.com
Website: coralpennant.com
Requirements
Must have
- the current information of the business card provided.
logo
use the PMS Colors
Nice to have
- a touch of elegance and sophistication but simple
Should not have
- should not have any typography that is hard to read, the card should be simple but yet sophisticated.

```html
<!DOCTYPE html>
<html lang="en">
<head>
<meta charset="utf-8">
<title>Coral Pennant – Business Card</title>
<link href="https://fonts.googleapis.com/css2?family=Poppins:wght@400;500;600&display=swap" rel="stylesheet">
<style>
  :root {
    --bg: #e6e6e6;
    --blue-deep: #1d5aa3;
    --blue-light: #3987c8;
    --orange: #f08a24;
    --white: #ffffff;
  }
  html, body { margin: 0; padding: 0; width: 1200px; height: 1200px; overflow: hidden; background: var(--bg); }
  body { position: relative; font-family: "Poppins", sans-serif; }
  .card {
    position: absolute; left: 257px; width: 686px; height: 392px;
    border-radius: 18px; overflow: hidden;
  }
  .card-front { top: 165px; background: var(--white); }
  .card-back { top: 653px; background: linear-gradient(135deg, var(--blue-deep) 20%, var(--blue-light) 100%); }
  .front-wave { position: absolute; inset: 0; }
  .brand { position: absolute; left: 0; right: 0; text-align: center; }
  .brand-mark {
    width: 66px; height: 66px; border-radius: 50%;
    border: 7px solid var(--blue-deep); box-sizing: border-box;
    margin: 0 auto;
  }
  .brand-front { top: 42px; }
  .brand-name {
    margin-top: 24px; font-weight: 600; font-size: 27px; letter-spacing: 1px;
    color: var(--blue-deep); text-transform: uppercase; line-height: 1;
  }
  .brand-tagline {
    margin-top: 10px; font-weight: 500; font-size: 18px; color: var(--blue-deep);
    letter-spacing: 0.5px; line-height: 1;
  }
  .contact-left {
    position: absolute; right: 378px; top: 276px; text-align: right;
    color: var(--white); font-size: 15.5px; line-height: 19.5px;
  }
  .contact-name { color: var(--orange); font-weight: 500; font-size: 22px; line-height: 26px; text-transform: uppercase; margin-bottom: 1px; }
  .divider { position: absolute; left: 332px; top: 280px; width: 1px; height: 92px; background: rgba(255,255,255,0.55); }
  .contact-right { position: absolute; left: 354px; top: 279px; margin: 0; padding: 0; list-style: none; color: var(--white); font-size: 15.5px; line-height: 19.5px; }
  .contact-right li { display: flex; align-items: center; gap: 9px; }
  .contact-right svg { width: 13px; height: 13px; fill: var(--orange); flex: none; }
  .brand-back { top: 98px; }
  .brand-back .brand-mark { width: 110px; height: 110px; border: 10px solid var(--white); opacity: 0.9; }
  .brand-back .brand-name { color: var(--white); font-size: 30px; margin-top: 22px; }
  .back-web {
    position: absolute; left: 0; right: 0; top: 340px; text-align: center;
    color: var(--white); font-size: 15.5px; letter-spacing: 3.6px;
  }
</style>
</head>
<body>
  <section class="card card-front">
    <svg class="front-wave" viewBox="0 0 686 392" preserveAspectRatio="none" aria-hidden="true">
      <defs>
        <linearGradient id="bandBlue" x1="0" y1="1" x2="1" y2="0">
          <stop offset="0" stop-color="#1d5aa3"/>
          <stop offset="1" stop-color="#3987c8"/>
        </linearGradient>
      </defs>
      <path d="M0 276 Q343 188 686 282 L686 392 L0 392 Z" fill="#f08a24"/>
      <path d="M0 283 Q343 196 686 288 L686 392 L0 392 Z" fill="url(#bandBlue)"/>
    </svg>
    <div class="brand brand-front">
      <div class="brand-mark"></div>
      <div class="brand-name">Coral Pennant</div>
      <div class="brand-tagline">MARINE CENTER</div>
    </div>
    <div class="contact-left">
      <div class="contact-name">Dale Whitcombe</div>
      <div>212 North Fenwick Lane</div>
      <div>Harbor Point, FL 33120</div>
      <div>www.coralpennant.com</div>
    </div>
    <div class="divider"></div>
    <ul class="contact-right">
      <li><svg viewBox="0 0 24 24"><path d="M6.6 10.8a15.1 15.1 0 0 0 6.6 6.6l2.2-2.2a1 1 0 0 1 1-.25 11.4 11.4 0 0 0 3.6.57 1 1 0 0 1 1 1V20a1 1 0 0 1-1 1A17 17 0 0 1 3 4a1 1 0 0 1 1-1h3.5a1 1 0 0 1 1 1c0 1.25.2 2.45.57 3.570a1 1 0 0 1-.25 1z"/></svg>954-731-8842</li>
      <li><svg viewBox="0 0 24 24"><path d="M7 1h10a2 2 0 0 1 2 2v18a2 2 0 0 1-2 2H7a2 2 0 0 1-2-2V3a2 2 0 0 1 2-2zm0 3v14h10V4z"/></svg>954-382-1490</li>
      <li><svg viewBox="0 0 24 24"><path d="M6 2h12v6H6zM3 9h18a1 1 0 0 1 1 1v8h-4v4H6v-4H2v-8a1 1 0 0 1 1-1zm5 7v4h8v-4z"/></svg>954-731-8843</li>
      <li><svg viewBox="0 0 24 24"><path d="M2 5h20v14H2zm2 2v.5l8 5 8-5V7z"/></svg>dw@coralpennant.com</li>
    </ul>
  </section>

  <section class="card card-back">
    <div class="brand brand-back">
      <div class="brand-mark"></div>
      <div class="brand-name">Coral Pennant</div>
    </div>
    <div class="back-web">WWW.CORALPENNANT.COM</div>
  </section>
</body>
</html>
```